Homemaking training schools needs a Business Card design

Designer, Hello!

No special requirements, good-looking enough.
--------------------------------------------------------------------------

Name: Marcus Dole
Chairman
Tel: 0574-71948263
Mobile: 13857420916
Email: kelvora@mailnest.example
Web: www.prt2019.example
Add: No.258, LanpingJie, BeiyuanQu, Ningbo, Zhejiang

LOGO
Ningbo PRT Homemaking Training School

Target Market(s)

pregnant women, mothers, infants, the elderly and families, including cleaning, cooking, nursing training.

Industry/Entity Type

Business

Contact Information for Business Card

Name: Marcus Dole
Chairman
Tel: 0574-71948263
Mobile: 13857420916
Email: kelvora@mailnest.example
Web: www.prt2019.example

LOGO

Font styles to use
Serif
Sans Serif
Decorative

Requirements
Nice to have
• Feels: clean, specifications, safety, comfort, warmth and happiness.

```html
<!DOCTYPE html>
<html lang="en">
<head>
<meta charset="utf-8">
<title>PingRuiTang Business Card</title>
<link href="https://fonts.googleapis.com/css2?family=Lato:wght@400;700&display=swap" rel="stylesheet">
<style>
  :root {
    --brand-blue: #3a78b9;
    --brand-magenta: #c0168f;
    --ink: #1c1c1c;
    --paper: #ffffff;
    --backdrop: #e6e7ea;
    --divider: #555555;
  }
  * { box-sizing: border-box; margin: 0; padding: 0; }
  html, body {
    width: 1200px; height: 900px; overflow: hidden;
    background: var(--backdrop);
    font-family: 'Lato', sans-serif;
  }
  .card {
    position: absolute;
    width: 600px; height: 340px;
    left: 300px;
    box-shadow: 0 6px 18px rgba(0,0,0,0.18);
    overflow: hidden;
  }
  /* Back side */
  .card-back { top: 100px; background: var(--brand-blue); color: var(--paper); }
  .card-back .wordmark {
    position: absolute; left: 0; right: 0; top: 92px;
    text-align: center; font-weight: 700; font-size: 58px; letter-spacing: 0.5px;
  }
  .tagline-row {
    position: absolute; display: flex; align-items: center; gap: 10px;
  }
  .tagline-row .rule { height: 1px; background: currentColor; flex: 1; }
  .tagline-row .tagline { font-size: 17px; letter-spacing: 1px; white-space: nowrap; }
  .card-back .tagline-row { left: 80px; right: 80px; top: 178px; }
  .card-back .web {
    position: absolute; left: 0; right: 0; top: 236px;
    text-align: center; font-size: 16px; letter-spacing: 3px;
  }

  /* Front side */
  .card-front { top: 460px; background: var(--paper); }
  .card-front .swoosh { position: absolute; inset: 0; }
  .card-front .wordmark {
    position: absolute; left: 34px; top: 58px; width: 232px;
    text-align: center;
    font-weight: 700; font-size: 38px; color: var(--brand-blue);
  }
  .card-front .tagline-row { left: 34px; width: 232px; top: 112px; color: var(--divider); }
  .card-front .tagline-row .tagline { font-size: 13px; }
  .card-front .divider {
    position: absolute; left: 298px; top: 40px; width: 1px; height: 150px;
    background: linear-gradient(to bottom, transparent, var(--divider), transparent);
  }
  .contact { position: absolute; left: 320px; top: 44px; color: var(--ink); }
  .contact .person { font-size: 26px; font-weight: 400; line-height: 1.1; }
  .contact .role { font-size: 16px; color: var(--brand-magenta); margin-bottom: 8px; }
  .contact .address { font-size: 14px; line-height: 1.35; margin-bottom: 4px; }
  .contact .line { display: flex; align-items: center; gap: 8px; font-size: 14px; line-height: 1.45; }
  .contact .line svg { width: 13px; height: 13px; fill: var(--brand-magenta); flex: none; }
  .card-front .web {
    position: absolute; left: 50px; top: 270px;
    color: var(--paper); font-size: 17px; letter-spacing: 1px;
    transform: rotate(9deg); transform-origin: left center;
  }
</style>
</head>
<body>

<section class="card card-back">
  <div class="wordmark">PingRuiTang</div>
  <div class="tagline-row"><span class="rule"></span><span class="tagline">Training &amp; Services</span><span class="rule"></span></div>
  <div class="web">www.prt2019.example</div>
</section>

<section class="card card-front">
  <svg class="swoosh" viewBox="0 0 600 340" preserveAspectRatio="none">
    <path d="M0,172 C220,196 440,252 600,286 L600,340 L0,340 Z" fill="var(--brand-magenta)"/>
    <path d="M0,180 C220,210 440,278 600,308 L600,340 L0,340 Z" fill="var(--paper)"/>
    <path d="M0,186 C220,218 440,288 600,318 L600,340 L0,340 Z" fill="var(--brand-blue)"/>
  </svg>
  <div class="wordmark">PingRuiTang</div>
  <div class="tagline-row"><span class="rule"></span><span class="tagline">Training &amp; Services</span><span class="rule"></span></div>
  <div class="divider"></div>
  <div class="contact">
    <div class="person">Marcus Dole</div>
    <div class="role">Chairman</div>
    <div class="address">No.258, LanpingJie<br>BeiyuanQu, Ningbo, Zhejiang</div>
    <div class="line">
      <svg viewBox="0 0 24 24"><path d="M6.6 10.8a15.1 15.1 0 0 0 6.6 6.6l2.2-2.2a1 1 0 0 1 1-.25 11.4 11.4 0 0 0 3.6.57 1 1 0 0 1 1 1V20a1 1 0 0 1-1 1A17 17 0 0 1 3 4a1 1 0 0 1 1-1h3.5a1 1 0 0 1 1 1c0 1.25.2 2.450.57 3.6a1 1 0 0 1-.25 1z"/></svg>
      <span>0574-71948263</span>
    </div>
    <div class="line">
      <svg viewBox="0 0 24 24"><path d="M7 1h10a2 2 0 0 1 2 2v18a2 2 0 0 1-2 2H7a2 2 0 0 1-2-2V3a2 2 0 0 1 2-2zm0 3v14h10V4zm5 15.5a1 1 0 1 0 0 2 1 1 0 0 0 0-2z"/></svg>
      <span>13857420916</span>
    </div>
    <div class="line">
      <svg viewBox="0 0 24 24"><path d="M2 5h20v14H2zm2 2v.5l8 5 8-5V7zm0 2.8V17h16V9.8l-8 5z"/></svg>
      <span>kelvora@mailnest.example</span>
    </div>
  </div>
  <div class="web">www.prt2019.example</div>
</section>

</body>
</html>
```